Business card design Needed for new logo / Construction business, home extensions and new builds

We need a business card design using our new logo files which i will attach to this project :)

We are a small construction business specialising in home extensions, new builds and property development. We are very ambitious and would appreciate professional and elegant designs for our new business card.

Very serious about using the services on MakerQuarry and recently acquired our new logo from here :)

Please get involved, i will feedback when i can as i am very busy but can respond daily, thanks

Target Market(s)

People that want to build onto their houses, new building developments or adding too their existing property

Industry/Entity Type

Construction

Contact Information for Business Card

Renwick Tolliver Construction, Lionel Ashby (Managing Director), Tel 07822254961, email - info@renwick-tolliver, www.renwick-tolliver.co.uk

Colors

Designer to choose colors to be used in the design.

Requirements
Must have
• I like a deep grey on the back please. A lot of you have provided black from and back, try mixing things up a little. The black looks cool 😎 Thanks

```html
<!DOCTYPE html>
<html lang="en">
<head>
<meta charset="utf-8">
<title>Renwick Tolliver Construction – Business Card</title>
<link rel="stylesheet" href="https://fonts.googleapis.com/css2?family=Montserrat:wght@700&family=Open+Sans:wght@400;600&display=swap">
<style>
  :root {
    --backdrop: #3b3b3d;
    --card: #141414;
    --gold: #d9a638;
    --gold-light: #f4cf6a;
    --gold-deep: #b7801f;
    --text-light: #e9e9e9;
  }
  * { box-sizing: border-box; margin: 0; padding: 0; }
  html, body {
    width: 1200px; height: 689px; overflow: hidden;
    background: var(--backdrop);
  }
  .canvas {
    position: relative; width: 1200px; height: 689px;
    display: flex; align-items: center; justify-content: center; gap: 60px;
  }
  .card {
    position: relative; width: 520px; height: 297px;
    background: var(--card);
    box-shadow: 0 18px 40px rgba(0,0,0,.45);
    overflow: hidden;
  }
  .card__band {
    position: absolute; left: 0; right: 0; bottom: 9px; height: 7px;
    background: linear-gradient(90deg, var(--gold-deep), var(--gold-light) 45%, var(--gold) 70%, var(--gold-deep));
  }
  .brand {
    display: flex; align-items: center; gap: 10px;
    font-family: "Open Sans", sans-serif; font-weight: 600;
    color: var(--gold); text-transform: uppercase; letter-spacing: 2px;
  }
  .brand__mark { width: 12px; height: 12px; background: var(--gold); flex: none; }
  .card--front .brand {
    position: absolute; left: 50%; top: 45%; transform: translate(-50%, -50%);
    font-size: 17px; white-space: nowrap;
  }
  .card--back .brand {
    position: absolute; left: 34px; top: 132px;
    font-size: 14px; letter-spacing: 1.5px; line-height: 1.45;
    align-items: flex-start;
  }
  .card--back .brand__mark { margin-top: 5px; }
  .divider {
    position: absolute; left: 262px; top: 58px; width: 1px; height: 150px;
    background: var(--gold);
  }
  .contact {
    position: absolute; left: 288px; top: 62px;
    font-family: "Open Sans", sans-serif; color: var(--text-light);
  }
  .contact__name {
    font-family: "Montserrat", sans-serif; font-weight: 700;
    font-size: 17px; letter-spacing: 1px; color: var(--gold);
  }
  .contact__role { font-size: 12px; margin-top: 2px; }
  .contact__list { list-style: none; margin-top: 24px; }
  .contact__item {
    display: flex; align-items: center; gap: 8px;
    font-size: 11.5px; margin-bottom: 7px;
  }
  .contact__icon { width: 13px; height: 13px; flex: none; }
</style>
</head>
<body>
<main class="canvas">
  <section class="card card--front" aria-label="Card front">
    <div class="brand"><span class="brand__mark"></span>Renwick Tolliver</div>
    <div class="card__band"></div>
  </section>

  <section class="card card--back" aria-label="Card back">
    <div class="brand"><span class="brand__mark"></span><span>Renwick Tolliver<br>Construction</span></div>
    <div class="divider"></div>
    <div class="contact">
      <h1 class="contact__name">LIONEL ASHBY</h1>
      <p class="contact__role">Managing Director</p>
      <ul class="contact__list">
        <li class="contact__item">
          <svg class="contact__icon" viewBox="0 0 16 16"><circle cx="8" cy="8" r="8" fill="#d9a638"/><path d="M5 4.5l1.6-.4 1 2-1 .8c.5 1.1 1.3 1.9 2.4 2.4l.8-1 2 1-.4 1.6c-3.4.2-6.6-3-6.4-6.4z" fill="#141414"/></svg>
          07822254961
        </li>
        <li class="contact__item">
          <svg class="contact__icon" viewBox="0 0 16 16"><circle cx="8" cy="8" r="8" fill="#d9a638"/><rect x="4" y="5.5" width="8" height="5.5" fill="#141414"/><path d="M4 5.5l4 3 4-3" stroke="#d9a638" stroke-width="1" fill="none"/></svg>
          info@renwick-tolliver
        </li>
        <li class="contact__item">
          <svg class="contact__icon" viewBox="0 0 16 16"><circle cx="8" cy="8" r="8" fill="#d9a638"/><circle cx="8" cy="8" r="4" fill="none" stroke="#141414" stroke-width="1.2"/><path d="M4 8h8M8 4c-1.6 2.4-1.6 5.6 0 8M8 4c1.6 2.4 1.6 5.6 0 8" stroke="#141414" stroke-width="1" fill="none"/></svg>
          www.renwick-tolliver.co.uk
        </li>
      </ul>
    </div>
    <div class="card__band"></div>
  </section>
</main>
</body>
</html>
```